Brightarc Orthodontics appointment card design

I need appointment cards/ business cards made. Front will be Logo, name, title, email, phone number and location (5263 Walnut Hollow Pkwy, Ste 412, Concord, NC 28027) . the back should have an appointment card (name, time, date) and also 3 addresses listed with a check box so we can check to which location they are going.
Dale Fenwick Orthodontics
- 6735 Orchard Street, Ste 514, Harrisburg, NC 28075
- 3647 Ridgeway Drive NE, Ste 810, Concord, NC 28025
- 2917 Thornbury Corporate Drive, Ste 605, Charlotte, NC 28277
Business card can be horizontal or vertical in Design.
I need to be able to edit it to update and add new employees

Requirements
Must have
• Front:
• - Logo
• - Name & Title (able to be edited)
• - phone (704-555-0186) & Email (need to be able to edit)
• - Address: 5263 Walnut Hollow Pkwy, Ste 412
• Concord, NC 28027
• Back:
• Appointment Card design:
• - Name, time, Date
• - 3 locations w/ a check box so the patient knows where to go:
• Dale Fenwick Orthodontics
• - 6735 Orchard Street, Ste 514, Harrisburg, NC 28075
• - 3647 Ridgeway Drive NE, Ste 810, Concord, NC 28025
• - 2917 Thornbury Corporate Drive, Ste 605, Charlotte, NC 28277

```html
<!DOCTYPE html>
<html lang="en">
<head>
<meta charset="utf-8">
<title>Brightarc Orthodontics – Business &amp; Appointment Card</title>
<link rel="stylesheet" href="https://fonts.googleapis.com/css2?family=Lato:wght@400;700;900&family=Oswald:wght@600&display=swap">
<style>
  :root{
    --blue:#1f6fb8;
    --navy:#232a38;
    --rule:#3a4254;
    --paper:#f1f1f2;
    --white:#ffffff;
    --grey:#6d6f73;
    --ink:#1c1f26;
    --stage:#2b2d31;
  }
  *{box-sizing:border-box;margin:0;padding:0}
  html,body{width:1200px;height:1200px;overflow:hidden;background:var(--stage)}
  body{font-family:"Lato",sans-serif;position:relative}
  .card{position:absolute;left:120px;width:960px;height:549px;overflow:hidden;box-shadow:0 14px 30px rgba(0,0,0,.45)}
  .card--front{top:40px;background:var(--paper)}
  .card--back{top:611px;background:var(--white)}
  .card__shapes{position:absolute;inset:0}

  .wordmark{position:absolute;display:flex;flex-direction:column;align-items:flex-end;line-height:1}
  .wordmark__name{font-weight:900;color:var(--blue);letter-spacing:-1px}
  .wordmark__sub{font-weight:700;color:var(--grey);text-transform:uppercase}
  .card--front .wordmark{left:70px;top:250px}
  .card--front .wordmark__name{font-size:92px}
  .card--front .wordmark__sub{font-size:25px;letter-spacing:7px;margin-top:6px}
  .card--back .wordmark{right:80px;top:50px}
  .card--back .wordmark__name{font-size:64px}
  .card--back .wordmark__sub{font-size:17px;letter-spacing:5px;margin-top:4px}

  .person{position:absolute;right:70px;top:78px;text-align:right}
  .person__name{font-family:"Oswald",sans-serif;font-weight:600;font-size:36px;color:var(--blue);text-transform:uppercase;line-height:1}
  .person__title{font-size:19px;color:var(--white);margin-top:4px}
  .person__bar{position:absolute;right:32px;top:78px;width:14px;height:40px;border-radius:3px;background:var(--blue)}

  .contact{position:absolute;left:560px;right:0;top:225px;list-style:none}
  .contact__row{display:flex;justify-content:flex-end;align-items:center;gap:14px;padding:14px 36px 14px 0;border-top:1px solid var(--rule);color:var(--white);font-size:20px;text-align:right;line-height:1.25}
  .contact__row:last-child{border-bottom:1px solid var(--rule)}
  .contact__icon{width:18px;height:18px;flex:none;fill:var(--blue)}

  .form{position:absolute;left:60px;right:60px;top:190px;color:var(--ink)}
  .form__row{display:flex;align-items:flex-end;gap:10px;font-weight:900;font-size:26px;margin-bottom:26px}
  .form__line{flex:1;border-bottom:2px solid var(--blue);height:2px;margin-bottom:6px}
  .form__line--short{flex:.6}
  .form__label--gap{margin-left:20px}

  .locations{position:absolute;left:60px;top:330px;color:var(--ink)}
  .locations__heading{font-weight:900;font-size:26px;margin-bottom:12px;padding-left:42px}
  .locations__list{list-style:none}
  .locations__item{display:flex;align-items:center;gap:18px;font-size:26px;margin-bottom:10px}
  .checkbox{width:24px;height:24px;border:2px solid var(--blue);flex:none}
  .checkbox--checked{background:var(--blue)}
</style>
</head>
<body>

<section class="card card--front" aria-label="Business card front">
  <svg class="card__shapes" viewBox="0 0 960 549" preserveAspectRatio="none" aria-hidden="true">
    <polygon points="355,0 960,0 960,549 560,549 560,128" fill="var(--navy)"/>
    <polygon points="300,0 355,0 560,128 560,152" fill="var(--blue)"/>
  </svg>

  <div class="wordmark">
    <span class="wordmark__name">Brightarc</span>
    <span class="wordmark__sub">Orthodontics</span>
  </div>

  <div class="person">
    <p class="person__name">Evan Carter</p>
    <p class="person__title">CEO / Manager</p>
  </div>
  <span class="person__bar"></span>

  <ul class="contact">
    <li class="contact__row">+704-555-0186
      <svg class="contact__icon" viewBox="0 0 24 24"><path d="M6.6 10.8a15 15 0 0 0 6.6 6.6l2.2-2.2a1 1 0 0 1 1-.25 11.4 11.4 0 0 0 3.6.6 1 1 0 0 1 1 1V20a1 1 0 0 1-1 1A17 17 0 0 1 3 4a1 1 0 0 1 1-1h3.5a1 1 0 0 1 1 1c0 1.25.2 2.45.6 3.6a1 1 0 0 1-.25 1z"/></svg>
    </li>
    <li class="contact__row">frontdesk@brightarcortho.com
      <svg class="contact__icon" viewBox="0 0 24 24"><path d="M2 5h20v14H2z M2 5l10 8 10-8" stroke="var(--navy)" stroke-width="1.5"/></svg>
    </li>
    <li class="contact__row">www.brightarcortho.com
      <svg class="contact__icon" viewBox="0 0 24 24"><circle cx="12" cy="12" r="10"/><path d="M2 12h20M12 2c3 3 3 17 0 20M12 2c-3 3-3 17 0 20" stroke="var(--navy)" stroke-width="1.4" fill="none"/></svg>
    </li>
    <li class="contact__row">5263 Walnut Hollow Pkwy<br>Ste 412 - Concord, NC 28027
      <svg class="contact__icon" viewBox="0 0 24 24"><path d="M12 2a7 7 0 0 0-7 7c0 5 7 13 7 13s7-8 7-13a7 7 0 0 0-7-7zm0 9.5A2.5 2.5 0 1 1 12 6.5a2.5 2.5 0 0 1 0 5z"/></svg>
    </li>
  </ul>
</section>

<section class="card card--back" aria-label="Appointment card back">
  <div class="wordmark">
    <span class="wordmark__name">Brightarc</span>
    <span class="wordmark__sub">Orthodontics</span>
  </div>

  <div class="form">
    <div class="form__row">
      <span>Name :</span><span class="form__line"></span>
      <span class="form__label--gap">Date :</span><span class="form__line form__line--short"></span>
    </div>
    <div class="form__row">
      <span>Time :</span><span class="form__line"></span>
    </div>
  </div>

  <div class="locations">
    <p class="locations__heading">Dale Fenwick Orthodontics :</p>
    <ul class="locations__list">
      <li class="locations__item"><span class="checkbox checkbox--checked"></span>6735 Orchard Street, Ste 514, Harrisburg, NC 28075</li>
      <li class="locations__item"><span class="checkbox"></span>3647 Ridgeway Drive NE, Ste 810, Concord, NC 28025</li>
      <li class="locations__item"><span class="checkbox"></span>2917 Thornbury Corporate Drive, Ste 605, Charlotte, NC 28277</li>
    </ul>
  </div>
</section>

</body>
</html>
```